Real Estate Webpage Design

We have an existing website: ferndaleestatecollective.com.au
We focus customised service mainly on Property Management and second-hand property sales.
We are not entirely happy about the current design and layout can stay roughly the same as the back end coding is linked to a CRM system.
We would like to see the design are more reachable to our clients and appearing.
Please check our Website Design Draft for more details.

Industry/Entity Type

Real estate Agency

Number of Pages Required

5+ page

Font styles to use
Sans Serif

Colors

Designer to choose colors to be used in the design.

```html
<!DOCTYPE html>
<html lang="en">
<head>
<meta charset="utf-8">
<title>La Morada Property Group</title>
<link href="https://fonts.googleapis.com/css2?family=Poppins:wght@500;600;700;800&family=Lato:ital,wght@0,400;0,700;1,400&display=swap" rel="stylesheet">
<style>
:root{
  --gold:#f5a623;
  --gold-deep:#e8961a;
  --dark:#2f3542;
  --ink:#2a2a2a;
  --text:#5a5a5a;
  --line:#cfcfcf;
  --white:#ffffff;
}
*{box-sizing:border-box;margin:0;padding:0}
html,body{width:1200px;height:3331px;overflow:hidden}
body{position:relative;background:var(--white);font-family:"Lato",sans-serif;color:var(--text)}
.abs{position:absolute}
.heading{font-family:"Poppins",sans-serif;font-weight:700;color:var(--ink)}

/* header */
.hero-photo{left:0;top:0;width:1200px;height:780px;background:linear-gradient(180deg,#eef2ee 0%,#d6e2d0 10%,#4f7a3f 30%,#3d6530 45%,#b9a894 62%,#e6dccb 72%,#5d8a45 88%,#6f9a50 100%)}
.top-call{right:144px;top:18px;display:flex;align-items:center;gap:8px;font-family:"Poppins",sans-serif;font-weight:600;font-size:19px;color:var(--ink)}
.top-call .ring{width:30px;height:30px;border:2px solid var(--gold);border-radius:50%;display:flex;align-items:center;justify-content:center}
.brand{left:146px;top:48px;display:flex;align-items:center;gap:10px}
.brand .mark{width:44px;height:44px;background:var(--gold)}
.brand .name{font-family:"Poppins",sans-serif;font-weight:600;font-size:32px;color:var(--dark);line-height:1}
.nav{left:405px;top:62px;display:flex;gap:24px;font-family:"Poppins",sans-serif;font-weight:600;font-size:12.5px;color:var(--ink)}
.nav .search{width:12px;height:12px;border:2px solid var(--gold);border-radius:50%}

/* intro */
.intro-sheet{left:0;top:575px;width:1087px;height:460px;background:var(--white);border-top-right-radius:300px}
.intro-base{left:0;top:780px;width:1200px;height:255px;background:var(--white)}
.scroll{left:1118px;top:704px;width:60px;text-align:center;color:var(--white);font-size:6px;font-family:"Poppins",sans-serif;letter-spacing:.3px}
.scroll .ring{margin:5px auto 0;width:32px;height:32px;border:2px solid var(--white);border-radius:50%;display:flex;align-items:center;justify-content:center}
.intro-title{left:142px;top:626px;font-size:40px;line-height:57px;font-weight:700}
.intro-title em{font-style:normal;color:var(--gold)}
.intro-copy{left:142px;top:757px;width:490px;font-size:14.2px;line-height:24px}
.intro-copy p+p{margin-top:24px}
.intro-badge{left:670px;top:627px;width:330px;height:330px;display:flex;flex-direction:column;align-items:center;justify-content:center;gap:22px}
.intro-badge .sq{width:120px;height:120px;background:var(--gold)}
.intro-badge .nm{font-family:"Poppins",sans-serif;font-weight:700;font-size:40px;color:var(--dark)}

/* banner */
.month-band{left:0;top:1031px;width:1200px;height:80px;background:var(--gold)}
.month-title{left:0;top:1031px;width:1200px;height:80px;line-height:80px;text-align:center;font-family:"Poppins",sans-serif;font-weight:700;font-size:40px;color:var(--white)}
.tabs{left:147px;top:1139px;display:flex;gap:13px}
.tab{width:171px;height:51px;border:2px solid var(--dark);border-radius:26px;display:flex;align-items:center;justify-content:center;font-family:"Poppins",sans-serif;font-weight:600;font-size:14px;color:var(--dark)}
.tab.is-active{background:var(--dark);color:var(--white)}

/* listings */
.card{top:1230px;width:296px}
.card-photo{width:296px;height:186px;position:relative}
.card-photo svg{position:absolute;left:0;bottom:0}
.card-body{padding:20px 0 0 24px}
.suburb{font-family:"Poppins",sans-serif;font-weight:600;font-size:16px;color:var(--ink)}
.address{font-family:"Poppins",sans-serif;font-weight:600;font-size:16px;color:var(--ink);margin-top:2px}
.price-row{display:flex;align-items:center;gap:12px;margin-top:10px}
.price{font-family:"Poppins",sans-serif;font-weight:700;font-size:23px;color:var(--gold)}
.feats{display:flex;gap:8px;font-size:9px;color:var(--ink)}
.inspect{margin-top:12px;font-size:17px;color:var(--ink)}
.time{margin-top:6px;font-size:13px;color:var(--text);display:flex;align-items:center;gap:10px}
.dot{width:13px;height:13px;border-radius:50%;background:var(--gold)}
.actions{display:flex;gap:7px;margin-top:18px}
.act{width:26px;height:26px;border-radius:50%;background:var(--gold);display:flex;align-items:center;justify-content:center}
.act.dark{background:var(--dark)}
.card-rule{margin-top:12px;width:240px;height:2px;background:var(--gold)}
.arrow-btn{width:44px;height:44px;border:1.5px solid #777;border-radius:50%;display:flex;align-items:center;justify-content:center}

/* testimonials */
.testi{left:22px;top:1737px;width:1156px;height:469px;border-radius:235px;background:linear-gradient(90deg,#2f3542 0%,#5d5240 40%,#c58f2e 70%,#f5a623 100%)}
.testi-title{left:0;top:1795px;width:1200px;text-align:center;font-family:"Poppins",sans-serif;font-weight:700;font-size:42px;color:var(--white)}
.testi-quote{left:265px;top:1864px;width:670px;text-align:center;font-style:italic;font-size:16px;line-height:26.5px;color:var(--white)}
.testi-name{left:0;top:2029px;width:1200px;display:flex;justify-content:center;align-items:center;gap:18px;font-family:"Poppins",sans-serif;font-weight:600;font-size:17px;color:var(--white)}
.stars{display:flex;gap:3px}
.testi-nav{left:551px;top:2092px;display:flex;gap:9px}
.testi-nav .arrow-btn{border-color:var(--gold)}
.testi-nav .arrow-btn.light{border-color:var(--white)}

/* contact */
.contact-bg{left:0;top:2200px;width:1200px;height:775px;background:linear-gradient(180deg,#ffffff 0%,#f1efed 25%,#d9d4cf 55%,#c9c3bc 80%,#eeeeee 100%)}
.contact-fade{left:0;top:2200px;width:1200px;height:775px;background:linear-gradient(90deg,rgba(255,255,255,.2) 0%,rgba(255,255,255,.55) 50%,rgba(255,255,255,.95) 100%)}
.contact-title{left:0;top:2285px;width:1200px;text-align:center;font-size:42px}
.contact-title em{font-style:normal;color:var(--gold)}
.pin{top:2385px;width:110px;height:122px}
.pin-label{top:2528px;width:240px;text-align:center;font-size:14px;line-height:23px;color:var(--ink)}
.pin-label.strong{font-family:"Poppins",sans-serif;font-weight:600;font-size:13.5px}
.field{height:41px;border:1.5px solid #8a8a8a;border-radius:21px;background:var(--white);padding:13px 28px;font-size:12.5px;color:var(--ink)}
.submit{left:504px;top:2854px;width:192px;height:48px;border-radius:24px;background:var(--gold);display:flex;align-items:center;justify-content:center;gap:8px;font-family:"Poppins",sans-serif;font-weight:600;font-size:14px;color:var(--white)}

/* footer */
.footer{left:0;top:2975px;width:1200px;height:356px;background:var(--dark)}
.foot-h{font-family:"Poppins",sans-serif;font-weight:700;font-size:38px;color:var(--gold)}
.hours{left:148px;top:3090px;font-size:14px;line-height:29px;color:var(--white)}
.hours span{display:inline-block;width:112px}
.vline{width:1px;height:165px;background:#555d6c;top:3022px}
.socials{left:508px;top:3105px;display:flex;gap:14px}
.soc{width:48px;height:48px;border:2px solid var(--white);border-radius:50%;display:flex;align-items:center;justify-content:center}
.soc.on{background:var(--gold);border-color:var(--gold)}
.soc i{width:8px;height:8px;border-radius:50%;background:var(--white)}
.foot-brand{left:845px;top:3030px;width:225px;text-align:center}
.foot-brand .sq{width:90px;height:90px;background:var(--gold);margin:0 auto 16px}
.foot-brand .nm{font-family:"Poppins",sans-serif;font-weight:600;font-size:40px;line-height:44px;color:var(--white)}
.foot-brand .sub{font-family:"Poppins",sans-serif;font-weight:600;font-size:11px;color:var(--white)}
.copy{left:0;top:3255px;width:1200px;text-align:center;font-size:14px;color:var(--white)}
</style>
</head>
<body>

<!-- header & hero -->
<div class="abs hero-photo" role="img" aria-label="Photograph of a large two-storey Spanish-style villa with terracotta roof, white walls and green gardens"></div>
<div class="abs top-call"><span class="ring"><svg width="14" height="14" viewBox="0 0 24 24"><path fill="#f5a623" d="M6.6 10.8a15 15 0 0 0 6.6 6.6l2.2-2.2a1 1 0 0 1 1-.25 11.4 11.4 0 0 0 3.6.57 1 1 0 0 1 1 1V20a1 1 0 0 1-1 1A17 17 0 0 1 3 4a1 1 0 0 1 1-1h3.5a1 1 0 0 1 1 1c0 1.25.2 2.45.57 3.57a1 1 0 0 1-.25 1z"/></svg></span>CALL : 02 5550 1234</div>
<div class="abs brand"><span class="mark"></span><span class="name">La Morada</span></div>
<nav class="abs nav"><span>HOME</span><span>ABOUT US</span><span>LEASING</span><span>BUY</span><span>SELL</span><span>OUR TEAM</span><span>BLOG</span><span>CONTACT US</span><span>EN ▾</span><span class="search"></span></nav>

<!-- intro -->
<div class="abs intro-base"></div>
<div class="abs intro-sheet"></div>
<div class="abs scroll">SCROLL DOWN<div class="ring"><svg width="14" height="10" viewBox="0 0 14 10"><path d="M1 2l6 6 6-6" stroke="#fff" stroke-width="2" fill="none"/></svg></div></div>
<h1 class="abs heading intro-title">La Morada – Spanish<br>for <em>“the dwelling”</em></h1>
<div class="abs intro-copy">
  <p>La Morada in Spanish means “the dwelling, the home”, buying a property is one of the most expensive expenses and important assets for people. La Morada is a real estate company located in Gungahlin, Canberra.</p>
  <p>Being a portfolio sales agent and property manager, coupled with our high–profile international real estate experience, La Morada is considered a market leader on the cutting edge with deep industry knowledge, ranging from landlord–tenant relationships, residential purchases.</p>
</div>
<div class="abs intro-badge"><span class="sq"></span><span class="nm">La Morada</span></div>

<!-- this month -->
<div class="abs month-band"></div>
<svg class="abs" style="left:1012px;top:1031px" width="188" height="80" viewBox="0 0 188 80"><path d="M60 0H188V80H0Z" fill="#2f3542"/><path d="M85 80L130 36H166V80H150V52H136L108 80Z" fill="#f5a623"/></svg>
<h2 class="abs month-title">This Month At La Morada Property Group</h2>
<div class="abs tabs">
  <span class="tab is-active">FOR SALE</span><span class="tab">FOR LEASE</span><span class="tab">OPEN TIMES</span><span class="tab">SOLD</span><span class="tab">LEASED</span>
</div>

<div class="abs arrow-btn" style="left:69px;top:1418px"><svg width="10" height="16" viewBox="0 0 10 16"><path d="M8 1L2 8l6 7" stroke="#444" stroke-width="2" fill="none"/></svg></div>
<div class="abs arrow-btn" style="left:1086px;top:1418px"><svg width="10" height="16" viewBox="0 0 10 16"><path d="M2 1l6 7-6 7" stroke="#444" stroke-width="2" fill="none"/></svg></div>

<article class="abs card" style="left:145px">
  <div class="card-photo" role="img" aria-label="Photo of a rooftop pool beside an apartment tower" style="background:linear-gradient(135deg,#7d8c92 0%,#a9c2d6 45%,#3d6fa8 75%,#b26a3a 100%)"><svg width="296" height="40" viewBox="0 0 296 40"><path d="M0 40V38L148 0 296 38V40Z" fill="#fff"/><path d="M0 38L148 0 296 38" stroke="#f5a623" stroke-width="5" fill="none"/></svg></div>
  <div class="card-body">
    <div class="suburb">GUNGAHLIN</div><div class="address">Level 5/12 Banksia Parade</div>
    <div class="price-row"><span class="price">$500,000+</span><span class="feats"><span>▭ 2</span><span>▭ 2</span><span>▭ 1</span></span></div>
    <div class="inspect">Next Inspection:</div>
    <div class="time"><span class="dot"></span>Sat 21st May 09:40 AM - 10:00 AM</div>
    <div class="actions"><span class="act"></span><span class="act dark"></span><span class="act"></span></div>
    <div class="card-rule"></div>
  </div>
</article>
<article class="abs card" style="left:452px">
  <div class="card-photo" role="img" aria-label="Photo of a white apartment block with pink balconies under a blue sky" style="background:linear-gradient(135deg,#2f7fd0 0%,#dfe6ee 40%,#c78a95 60%,#3f6a2e 100%)"><svg width="296" height="40" viewBox="0 0 296 40"><path d="M0 40V38L148 0 296 38V40Z" fill="#fff"/><path d="M0 38L148 0 296 38" stroke="#f5a623" stroke-width="5" fill="none"/></svg></div>
  <div class="card-body">
    <div class="suburb">BELCONNEN</div><div class="address">172/40 Kestrel Street Belconnen</div>
    <div class="price-row"><span class="price">$500,000+</span><span class="feats"><span>▭ 2</span><span>▭ 2</span><span>▭ 1</span></span></div>
    <div class="inspect">Next Inspection:</div>
    <div class="time"><span class="dot"></span>Sat 21st May 09:40 AM - 10:00 AM</div>
    <div class="actions"><span class="act"></span><span class="act dark"></span><span class="act"></span></div>
    <div class="card-rule"></div>
  </div>
</article>
<article class="abs card" style="left:760px">
  <div class="card-photo" role="img" aria-label="Photo of a modern white house with large glass doors" style="background:linear-gradient(135deg,#3f86c9 0%,#f1f1ef 40%,#4a4a48 70%,#5c7f3a 100%)"><svg width="296" height="40" viewBox="0 0 296 40"><path d="M0 40V38L148 0 296 38V40Z" fill="#fff"/><path d="M0 38L148 0 296 38" stroke="#f5a623" stroke-width="5" fill="none"/></svg></div>
  <div class="card-body">
    <div class="suburb">GUNGAHLIN</div><div class="address">Level 5/12 Banksia Parade</div>
    <div class="price-row"><span class="price">$500,000+</span><span class="feats"><span>▭ 2</span><span>▭ 2</span><span>▭ 1</span></span></div>
    <div class="inspect">Next Inspection:</div>
    <div class="time"><span class="dot"></span>Sat 21st May 09:40 AM - 10:00 AM</div>
    <div class="actions"><span class="act"></span><span class="act dark"></span><span class="act"></span></div>
    <div class="card-rule"></div>
  </div>
</article>

<!-- testimonials -->
<section class="abs testi"></section>
<h2 class="abs testi-title">Testimonials</h2>
<p class="abs testi-quote">They are a greatly professional, organized and experienced team with extensive knowledge and understanding of the local market. My husband and I were provided with excellent feedback in a simple language we could understand and advice throughout the house journey and we were very pleased with the results. We highly recommend La Morada property group to anyone buying, selling or In need of property management in the local area.</p>
<div class="abs testi-name">AMARA JO ELLIS<span class="stars">
  <svg width="100" height="18" viewBox="0 0 100 18"><g fill="#f5a623"><path id="st" d="M9 0l2.6 6 6.4.5-4.9 4.2 1.5 6.3L9 13.6 3.4 17l1.5-6.3L0 6.5 6.4 6z"/><use href="#st" x="20"/><use href="#st" x="40"/><use href="#st" x="60"/><use href="#st" x="80"/></g></svg></span></div>
<div class="abs testi-nav">
  <div class="arrow-btn"><svg width="10" height="16" viewBox="0 0 10 16"><path d="M8 1L2 8l6 7" stroke="#f5a623" stroke-width="2" fill="none"/></svg></div>
  <div class="arrow-btn light"><svg width="10" height="16" viewBox="0 0 10 16"><path d="M2 1l6 7-6 7" stroke="#fff" stroke-width="2" fill="none"/></svg></div>
</div>

<!-- contact -->
<div class="abs contact-bg" role="img" aria-label="Faded photograph of apartment buildings and a street with parked cars"></div>
<div class="abs contact-fade"></div>
<h2 class="abs heading contact-title">Contact <em>Us</em></h2>

<svg class="abs pin" style="left:198px" viewBox="0 0 110 122"><path d="M55 120L30 95A53 53 0 1 1 80 95Z" fill="#fff" stroke="#f5a623" stroke-width="3"/><circle cx="55" cy="54" r="44" fill="#2f3542"/><path d="M42 40c3-2 6 5 4 7l-2 2c2 5 6 9 11 11l2-2c2-2 9 1 7 4l-2 4c-12 2-26-12-24-24z" fill="#fff"/></svg>
<svg class="abs pin" style="left:398px" viewBox="0 0 110 122"><path d="M55 120L30 95A53 53 0 1 1 80 95Z" fill="#fff" stroke="#f5a623" stroke-width="3"/><circle cx="55" cy="54" r="44" fill="#f5a623"/><path d="M36 56L55 38 74 56H68V72H60V62H50V72H42V56Z" fill="#fff"/></svg>
<svg class="abs pin" style="left:630px" viewBox="0 0 110 122"><path d="M55 120L30 95A53 53 0 1 1 80 95Z" fill="#fff" stroke="#f5a623" stroke-width="3"/><circle cx="55" cy="54" r="44" fill="#2f3542"/><rect x="36" y="44" width="8" height="28" fill="#fff"/><rect x="47" y="34" width="26" height="38" rx="2" fill="#fff"/><g fill="#2f3542"><rect x="52" y="40" width="16" height="7"/><rect x="52" y="52" width="4" height="4"/><rect x="60" y="52" width="4" height="4"/><rect x="52" y="60" width="4" height="4"/><rect x="60" y="60" width="4" height="4"/></g></svg>
<svg class="abs pin" style="left:861px" viewBox="0 0 110 122"><path d="M55 120L30 95A53 53 0 1 1 80 95Z" fill="#fff" stroke="#f5a623" stroke-width="3"/><circle cx="55" cy="54" r="44" fill="#2f3542"/><rect x="34" y="40" width="42" height="30" rx="4" fill="#fff"/><path d="M36 43l19 14 19-14" stroke="#2f3542" stroke-width="3" fill="none"/></svg>

<div class="abs pin-label" style="left:133px">Phone<br>02 5550 1234</div>
<div class="abs pin-label strong" style="left:335px">18/4 Wattlebird Lane,<br>Gungahlin, ACT, 2912</div>
<div class="abs pin-label" style="left:565px">Fax<br>02 5550 1299</div>
<div class="abs pin-label" style="left:796px">Email<br>info@lamoradagroup.com.au</div>

<div class="abs field" style="left:219px;top:2626px;width:372px">Enter Name</div>
<div class="abs field" style="left:609px;top:2626px;width:372px">Enter Email</div>
<div class="abs field" style="left:219px;top:2686px;width:372px">Phone</div>
<div class="abs field" style="left:609px;top:2686px;width:372px">Address</div>
<div class="abs field" style="left:219px;top:2746px;width:762px;height:73px">Message</div>
<div class="abs submit">SUBMIT MESSAGE <svg width="14" height="14" viewBox="0 0 14 14"><circle cx="7" cy="7" r="7" fill="#fff"/><path d="M5 4l3 3-3 3" stroke="#f5a623" stroke-width="2" fill="none"/></svg></div>

<!-- footer -->
<footer class="abs footer"></footer>
<h3 class="abs foot-h" style="left:147px;top:3020px">Hours</h3>
<div class="abs hours">
  <div><span>Monday – Friday</span>: &nbsp;8:30 am – 5:00pm</div>
  <div><span>Weekend</span>: &nbsp;Closed</div>
  <div><span>Public holiday</span>: &nbsp;Closed</div>
  <div>After hour by appointment</div>
</div>
<div class="abs vline" style="left:440px"></div>
<h3 class="abs foot-h" style="left:507px;top:3022px">Social</h3>
<div class="abs socials" aria-label="Social media links">
  <span class="soc"><i></i></span><span class="soc"><i></i></span><span class="soc on"><i></i></span><span class="soc"><i></i></span>
</div>
<div class="abs vline" style="left:801px"></div>
<div class="abs foot-brand"><div class="sq"></div><div class="nm">La Morada</div><div class="sub">Property Group</div></div>
<p class="abs copy">© 2022 La Morada . All rights reserved &nbsp;| &nbsp;Privacy &nbsp;| &nbsp;Terms of Use</p>

</body>
</html>
```